Flyer-Design für  junges, dynamisches Unternehmen, spezialisiert auf innovative Trainingskonzepte
Flyer-Design für junges, dynamisches Unternehmen, spezialisiert auf innovative Trainingskonzepte
volTEK
Sehr kreative und ideenreiche Umsetzungen. Alle Wünsche sind sehr sorgfältig, gewissenhaft und mit absoluter Schnelligkeit erfolgt.
Zielgruppe
Als junges dynamisches Unternehmen ist volTEK spezialisiert auf innovative Trainingskonzepte. Wir sind
ein international anerkanntes Trainingscenter der Northfield Rescue Council und bieten Notfalltrainings,
Erste-Hilfe-Kurse sowie hochwertige Simulationstrainings fur Rettungsdienste und Krankenhäuser an. In
unseren CRM- Simulationstrainings coachen wir Notfallteams in den Bereichen Skills, Human Factor und
Kommunikation. Hierbei kommen Full-Scale-Simulatoren und Schauspielpatienten zum Einsatz, die eine
realitätsnahe und lebensechte Trainingssituation präsentieren.
Aufgabenstellung
Wir suchen zur Vermarktung unserer Kurse eine graphische Übersicht, aus der die Qualitätsmerkmale von volTEK, eine Zielgruppen definition sowie eine detailierte Aufarbeitung der Kursinhalte in den Verschiedenen Kursformaten hervorgeht und unsere zukünftigen Kunden von uns überzeugt.
Großer Fokus dieses Projektes, ist es die Innenseite des Flyers zu gestalten, die ein geschlossenes Gesamtbild aufweisen soll. Deckblatt und Rückseite sind nebensächlich, hier freuen wir uns über neue Ideen, aber das Fokus ist die Gestaltung der Innenseite.

```html
<!DOCTYPE html>
<html lang="de">
<head>
<meta charset="utf-8">
<title>volTEK – Kursübersicht Innenseite</title>
<link href="https://fonts.googleapis.com/css2?family=Exo+2:ital,wght@1,700;1,800&family=Permanent+Marker&family=Encode+Sans+Condensed:wght@400;600&family=PT+Sans:ital,wght@0,400;1,400;1,700&display=swap" rel="stylesheet">
<style>
  :root{
    --red:#d71e26;
    --red-dark:#a8101a;
    --grey-panel:#e4e5e7;
    --text:#3c3c3c;
    --line:#4a4a4a;
    --white:#ffffff;
  }
  *{box-sizing:border-box;margin:0;padding:0}
  html,body{width:1200px;height:849px;overflow:hidden;background:var(--white)}
  .flyer{position:relative;width:1200px;height:849px;overflow:hidden;font-family:"PT Sans",sans-serif;color:var(--text)}
  .abs{position:absolute}

  .header-band,.footer-band{position:absolute;left:0;width:1200px}
  .header-band{top:0;height:80px}
  .footer-band{bottom:0;height:60px}
  .page-title{position:absolute;left:78px;top:16px;font-family:"Exo 2",sans-serif;font-style:italic;font-weight:800;font-size:17px;color:var(--white)}
  .web{position:absolute;right:75px;bottom:6px;font-family:"Exo 2",sans-serif;font-style:italic;font-weight:700;font-size:15px;color:var(--white);letter-spacing:.3px}

  .info-panel{position:absolute;left:601px;top:52px;width:599px;height:300px;background:var(--grey-panel)}
  .photo{position:absolute;top:52px;height:123px}
  .photo-1{left:602px;width:196px;background:linear-gradient(135deg,#6b4a3c,#c9a58a 55%,#3a2f2c)}
  .photo-2{left:808px;width:198px;background:linear-gradient(160deg,#5a4a40,#d2603a 50%,#3d3a3a)}
  .photo-3{left:1016px;width:184px;background:linear-gradient(140deg,#3a3030,#c54636 45%,#d8c4b4)}

  .course-intro{position:absolute;left:640px;top:190px;width:535px;font-size:9.6px;line-height:13.2px;color:#444}
  .course-intro p{margin-bottom:12.5px}
  .course-intro strong{font-style:italic;font-weight:700;color:var(--red);font-size:12px}

  .ribbon{position:absolute;width:236px;height:40px;background:linear-gradient(90deg,var(--red-dark),var(--red));color:var(--white);font-family:"Permanent Marker",cursive;font-size:8.6px;line-height:12px;display:flex;align-items:center;text-transform:uppercase}
  .ribbon.left{left:78px;padding-left:20px;clip-path:polygon(0 0,100% 0,91% 100%,0 100%)}
  .ribbon.right{left:325px;justify-content:flex-end;text-align:right;padding-right:20px;clip-path:polygon(9% 0,100% 0,100% 100%,0 100%);background:linear-gradient(90deg,var(--red),var(--red-dark))}
  .dot{position:absolute;width:11px;height:11px;border-radius:50%;background:var(--white);border:3px solid var(--red)}

  .section-title{position:absolute;left:78px;top:362px;font-family:"Exo 2",sans-serif;font-style:italic;font-weight:700;font-size:13px;color:#444}

  .tier-head{position:absolute;top:391px;width:200px;height:36px;display:flex;align-items:center;justify-content:center;font-family:"Encode Sans Condensed",sans-serif;font-weight:600;font-size:16px;color:var(--white);text-shadow:0 1px 2px rgba(0,0,0,.35);box-shadow:2px 2px 4px rgba(0,0,0,.18)}
  .tier-light{background:linear-gradient(#d9a85a,#fde58c)}
  .tier-basic{background:linear-gradient(#b9600c,#f5a462)}
  .tier-premium{background:linear-gradient(#9ea0a3,#e7e8e9)}
  .tier-plus{background:linear-gradient(#f3a000,#ffe800)}
  .tier-price{position:absolute;top:437px;font-family:"Encode Sans Condensed",sans-serif;font-weight:600;font-size:9.2px;color:#333}

  .topic{position:absolute;width:200px;height:36px;background:var(--white);box-shadow:1px 2px 5px rgba(0,0,0,.2);display:flex;align-items:center;padding:0 11px;font-family:"Encode Sans Condensed",sans-serif;font-size:8.6px;line-height:12px;color:#333}
  .topic.tall{height:86px}

  .partners{position:absolute;left:643px;top:671px;width:479px;height:100px;background:var(--white);box-shadow:0 1px 4px rgba(0,0,0,.15)}
  .partners-title{position:absolute;left:14px;top:8px;font-family:"Exo 2",sans-serif;font-style:italic;font-weight:700;font-size:8.5px;color:var(--red)}
  .badge{position:absolute;top:20px;width:46px;height:46px;border-radius:50%;border:1px solid #555;background:var(--white)}
  .badge-caption{position:absolute;top:73px;width:140px;text-align:center;font-family:"Encode Sans Condensed",sans-serif;font-weight:600;font-size:6.4px;line-height:9px;color:#777}

  .footnote{position:absolute;top:789px;width:1200px;text-align:center;font-style:italic;font-size:11px;color:#444}
</style>
</head>
<body>
<div class="flyer">

  <svg class="header-band" viewBox="0 0 1200 80" aria-hidden="true">
    <defs>
      <linearGradient id="hdrRed" x1="0" x2="1"><stop offset="0" stop-color="#a8101a"/><stop offset="1" stop-color="#e2222a"/></linearGradient>
    </defs>
    <path d="M0 0H1200V18C900 34 400 52 0 50Z" fill="url(#hdrRed)"/>
    <path d="M0 56C400 58 900 40 1200 24V30C900 48 400 66 0 74Z" fill="#5a5a5c"/>
  </svg>
  <div class="page-title">Was sind unsere Vorteile/Was zeichnet volTEK aus?</div>

  <div class="info-panel"></div>
  <div class="photo photo-1" role="img" aria-label="Foto: Reanimationstraining an einer Übungspuppe mit Beatmungsgerät"></div>
  <div class="photo photo-2" role="img" aria-label="Foto: Team im Notfalltraining mit Spritze und Defibrillator"></div>
  <div class="photo photo-3" role="img" aria-label="Foto: Beatmung mit Beutel-Maske bei einem Schauspielpatienten"></div>

  <div class="course-intro">
    <p><strong>Notfalltraining Light -</strong> Lernen Sie in diesem Skilltraining die Reanimation und beherrschen Sie die Herzdruckmassage. Außerdem besprechen wir die Intubation und die Defibrillation mit einem AED.</p>
    <p><strong>Notfalltraining Basic -</strong> Interaktives Team-Training: Üben Sie die wichtigsten Handgriffe und lernen Sie Ihre eigene Notfall­ausrüstung kennen. Das medizinische Know-How wird durch zusätzliche Themen wie Teamwork und Kommunikation erweitert.</p>
    <p><strong>Notfalltraining Premium -</strong> Weg mit der Puppe! Wir bringen unseren Schauspielpatienten mit zu Ihnen! Wir trainieren dynamische Notfälle und gemeinsam mit Ihnen analysieren und optimieren wir Ihr Notfallmanagement in Ihrer Praxis. Mit diesem Training schaffen Sie eine hohe Zufriedenheit mit Ihren Mitarbeitern und sind perfekt auf den nächsten Notfall vorbereitet. Auf Wunsch bieten wir Ihnen eine kostenlose Beratung und Verwaltung Ihrer Notfallausrüstung an.</p>
  </div>

  <div class="ribbon left" style="top:103px">Zertifizierte und anerkannte<br>Kurskonzepte</div>
  <div class="ribbon left" style="top:162px">Realistische Aus- und Fortbildung<br>mit Schauspielpatienten</div>
  <div class="ribbon left" style="top:221px">Alle Dozenten mit langjähriger<br>Erfahrung in der Notfallmedizin</div>
  <div class="ribbon left" style="top:281px">Durchführung der Schulungen bei<br>unseren Kunden inhouse vor Ort</div>
  <div class="ribbon right" style="top:103px">Angenehme Lernatmosphäre<br>mit emphatischen Instruktoren</div>
  <div class="ribbon right" style="top:162px">Modernstes Material,<br>Technik und Simulatoren</div>
  <div class="ribbon right" style="top:221px">Praxisorientierte und<br>individuelle Kursgestaltung</div>
  <div class="ribbon right" style="top:281px">Förderung der Teamarbeit<br>durch Crew Ressource Management</div>
  <span class="dot" style="left:73px;top:117px"></span>
  <span class="dot" style="left:73px;top:176px"></span>
  <span class="dot" style="left:73px;top:235px"></span>
  <span class="dot" style="left:73px;top:295px"></span>
  <span class="dot" style="left:554px;top:117px"></span>
  <span class="dot" style="left:554px;top:176px"></span>
  <span class="dot" style="left:554px;top:235px"></span>
  <span class="dot" style="left:554px;top:295px"></span>

  <div class="section-title">Kursdetails &amp; Preise</div>

  <svg class="abs" style="left:0;top:0" width="1200" height="849" aria-hidden="true">
    <g stroke="var(--line)" stroke-width="1" fill="none">
      <!-- Light -->
      <path d="M68 409H50V727H62"/>
      <path d="M50 473H62M50 524H62M50 575H62M50 626H62M50 676H62"/>
      <path d="M173 473V782H895"/>
      <!-- Basic -->
      <path d="M352 409H334V762H173"/>
      <path d="M334 473H346M334 524H346M334 575H346M334 626H346M334 676H346"/>
      <path d="M460 473V782"/>
      <!-- Premium -->
      <path d="M635 409H617V772H173"/>
      <path d="M617 473H629M617 524H629M617 600H629"/>
      <path d="M743 473V782"/>
      <!-- PremiumPLUS -->
      <path d="M913 409H895V782"/>
      <path d="M895 473H907M895 524H907M895 600H907"/>
    </g>
  </svg>

  <div class="tier-head tier-light" style="left:76px">Light</div>
  <div class="tier-head tier-basic" style="left:360px">Basic*</div>
  <div class="tier-head tier-premium" style="left:642px">Premium*</div>
  <div class="tier-head tier-plus" style="left:921px">PremiumPLUS*</div>

  <div class="tier-price" style="left:75px">2Std. | BLS | 1 Instruktor: 123,- €</div>
  <div class="tier-price" style="left:359px">3 Std. | 1 Instruktor | BLS + CRM: 234,- €</div>
  <div class="tier-price" style="left:642px">4 Std. | 1 Instruktor | BLS+CRM: 456,- €</div>
  <div class="tier-price" style="left:921px">Ab 4 Std. | 2 Intruktoren | BLS+ALS+CRM: 7890,- €</div>

  <div class="topic" style="left:76px;top:455px">Vorstellungen und Erläuterung des<br>Basic-Life-Support für med. Fachpersonal</div>
  <div class="topic" style="left:76px;top:506px">Auffinden eines bewusstlosen Patienten</div>
  <div class="topic" style="left:76px;top:557px">High-Performance-Reanimation, 5 Kriterien für<br>eine perfekte Herz-Druck-Massage</div>
  <div class="topic" style="left:76px;top:608px">Vorstellung Beutel-Masken-Beatmung, LTTubus<br>und Pocketmaske</div>
  <div class="topic" style="left:76px;top:658px">Vorstellung und Anwendung AED (Defi)</div>
  <div class="topic" style="left:76px;top:710px">Trainingsszenarien zum Ablauf einer Reanimation</div>

  <div class="topic" style="left:360px;top:455px">Übungen zur Beatmung für jeden Teilnehmer</div>
  <div class="topic" style="left:360px;top:506px">Übungen mit dem AED für jeden Teilnehmer</div>
  <div class="topic" style="left:360px;top:557px">Elektronische Auswertung der<br>Reanimationsergebnisse</div>
  <div class="topic" style="left:360px;top:608px">Training zur Teamkoordination und<br>Teamkommunikation</div>
  <div class="topic" style="left:360px;top:658px">Fallbeispiele zur Reanimation mit Feedback zur<br>Aufgabenbewältigung und Kommunikation</div>

  <div class="topic" style="left:642px;top:455px">Überprüfung und auf Wunsch Anpassung der<br>internen Abläufe der Rettungskette (QMNotfallplan)</div>
  <div class="topic" style="left:642px;top:506px">Fallbeispieltraining mit echtem Patienten<br>(Schauspieler)</div>
  <div class="topic tall" style="left:642px;top:557px">Fallbeispiel zu ausgewählten und passenden<br>Themen wie Asthma, Anaphylaxie,<br>Krampfanfall, Bolusgeschehen, Herzinfarkt,<br>etc. die Auswahl erfolgt Anhand der</div>

  <div class="topic" style="left:921px;top:455px">ABCDE-Schema zur Ersteinschätzung von<br>kritisch kranken Patienten</div>
  <div class="topic" style="left:921px;top:506px">FORDEC-Training zur Entscheidungsfindung</div>
  <div class="topic tall" style="left:921px;top:557px">Fallbeispiele zu lebensbedrohlichen<br>Situationen mit einem High-Tech-Simulator<br>u.a. mit Sprachfunktion, realistischen<br>Atembewegungen mit Atemgeräuschen,<br>Zyanose, tastebaren Pulsen und der</div>

  <div class="partners">
    <div class="partners-title">Wir sind ....</div>
    <span class="badge" style="left:76px"></span>
    <span class="badge" style="left:227px"></span>
    <span class="badge" style="left:381px"></span>
    <div class="badge-caption" style="left:29px">International anerkanntes Trainingscenter<br>der Northfield Rescue Council</div>
    <div class="badge-caption" style="left:180px">Partner und Förderer der GKSM e.V.</div>
    <div class="badge-caption" style="left:334px">Modernes Training unter Einsatz<br>von Video-Debriefing</div>
  </div>

  <div class="footnote">*Beinhaltet immer die vorrausgehenden Kurspackete</div>

  <svg class="footer-band" viewBox="0 0 1200 60" aria-hidden="true">
    <defs>
      <linearGradient id="ftrRed" x1="0" x2="1"><stop offset="0" stop-color="#e2222a"/><stop offset="1" stop-color="#a8101a"/></linearGradient>
    </defs>
    <path d="M260 36C600 26 900 18 1200 6V12C900 24 600 32 260 40Z" fill="#5a5a5c"/>
    <path d="M120 60C500 44 900 32 1200 18V60Z" fill="url(#ftrRed)"/>
  </svg>
  <div class="web">www.voltek-training.de</div>

</div>
</body>
</html>
```